Harbor Law Stationary - Law Firm

I am looking for a designer who can help me design letterhead and envelopes consistent with our new business cards. Feel free to reach out to me directly at ned@harborlawgroup.example. Thank you!! Visit harborlawgroup.example to see our site and the attached files for creative assets.

Target Market(s)

Anyone needing a lawyer

Font styles to use
Other font styles liked:
• Adobe Caslon Pro

Requirements
Must have
• Adobe Caslon Pro font
Full color
Nice to have
• My photo on front along with 2/3 face of camo - see mock up for example of what I have in mind.

American colors - similar to the ones found on my website and gold.

```html
<!DOCTYPE html>
<html lang="en">
<head>
<meta charset="utf-8">
<title>Harbor Law Stationery</title>
<link rel="stylesheet" href="https://fonts.googleapis.com/css2?family=Libre+Caslon+Text:wght@400;700&family=Arimo:wght@400&display=swap">
<style>
  :root {
    --navy: #0a2748;
    --gold: #b69a55;
    --backdrop: #7a7878;
    --paper: #ffffff;
    --ink: #3d3d3d;
    --rule: #1e2a3a;
    --badge-red: #c7333a;
    --badge-gold: #d9b53b;
  }
  * { margin: 0; padding: 0; box-sizing: border-box; }
  html, body { width: 1200px; height: 770px; overflow: hidden; }
  body { background: var(--backdrop); position: relative; font-family: "Arimo", Arial, sans-serif; }

  .sheet { position: absolute; background: var(--paper); overflow: hidden; }
  .wave { position: absolute; left: 0; top: 0; }

  /* Letterhead */
  .letterhead { left: 93px; top: 62px; width: 457px; height: 644px; }
  .brand { position: absolute; display: flex; align-items: center; gap: 10px; }
  .brand-dot { width: 22px; height: 22px; border-radius: 50%; background: var(--gold); flex: none; }
  .brand-name { font-family: "Libre Caslon Text", Georgia, serif; color: var(--gold); letter-spacing: 1px; text-transform: uppercase; }
  .letterhead .brand { left: 48px; top: 30px; }
  .letterhead .brand-name { font-size: 17px; line-height: 18px; }

  .contact { position: absolute; right: 44px; top: 33px; font-family: "Libre Caslon Text", Georgia, serif; font-size: 7px; color: #d8dbe2; text-align: right; line-height: 9.6px; }
  .contact li { list-style: none; display: flex; justify-content: flex-end; align-items: center; gap: 6px; }
  .contact li.gap { margin-top: 3px; }
  .contact svg { width: 7px; height: 7px; fill: var(--gold); flex: none; }

  .letter { position: absolute; left: 48px; top: 248px; width: 359px; color: var(--ink); }
  .salutation { font-size: 9.6px; margin-bottom: 12px; }
  .letter p.body { font-size: 6.7px; line-height: 10.8px; text-align: justify; margin-bottom: 11px; }
  .closing { font-size: 7px; margin-top: 26px; }
  .signature { display: block; width: 58px; height: 16px; margin-top: 14px; background: linear-gradient(90deg, #c9ccd3, #e6e8ec); border-radius: 3px; }

  .practice-footer { position: absolute; left: 48px; right: 43px; top: 590px; border-bottom: 1px solid var(--rule); padding-bottom: 6px; display: flex; justify-content: space-between; align-items: flex-end; }
  .practice-areas { font-family: "Libre Caslon Text", Georgia, serif; font-size: 7px; color: var(--navy); }
  .badges { display: flex; gap: 12px; margin-right: 6px; }
  .badge { width: 28px; height: 28px; border-radius: 50%; }
  .badge.red { border: 3px solid var(--badge-red); background: #fff; }
  .badge.gold { background: var(--badge-gold); border: 2px solid var(--navy); }

  /* Envelope back */
  .envelope-back { left: 644px; top: 331px; width: 508px; height: 251px; }
  .flap-mark { position: absolute; left: 0; right: 0; top: 33px; text-align: center; font-family: "Libre Caslon Text", Georgia, serif; font-size: 10px; color: var(--gold); letter-spacing: 1px; text-transform: uppercase; }

  /* Envelope front */
  .envelope-front { left: 584px; top: 455px; width: 510px; height: 251px; }
  .envelope-front .brand { left: 30px; top: 20px; align-items: flex-start; }
  .envelope-front .brand-dot { width: 20px; height: 20px; margin-top: 4px; }
  .envelope-front .brand-name { font-size: 15px; line-height: 18px; }
  .return-address { font-family: "Libre Caslon Text", Georgia, serif; font-size: 7.5px; line-height: 9.6px; color: #fff; margin-top: 6px; }
</style>
</head>
<body>

  <section class="sheet letterhead">
    <svg class="wave" width="457" height="120" viewBox="0 0 457 120">
      <path d="M0 0 H457 V22 C420 8 360 8 300 30 C220 60 150 110 70 98 C40 94 15 86 0 79 Z" fill="var(--navy)"/>
    </svg>

    <div class="brand">
      <span class="brand-dot"></span>
      <div class="brand-name">Harbor<br>Law</div>
    </div>

    <ul class="contact">
      <li>48 Quayside Avenue
        <svg viewBox="0 0 10 10"><path d="M5 0a3.5 3.5 0 0 0-3.5 3.5C1.5 6 5 10 5 10s3.5-4 3.5-6.5A3.5 3.5 0 0 0 5 0zm0 5a1.5 1.5 0 1 1 0-3 1.5 1.5 0 0 1 0 3z"/></svg></li>
      <li>Port Wren, Maine 04112 <svg viewBox="0 0 10 10"></svg></li>
      <li class="gap">(555)210-4471
        <svg viewBox="0 0 10 10"><path d="M2 0.5l2 2-1 1.2c.7 1.4 1.8 2.5 3.2 3.2l1.2-1 2 2-1.3 1.6C4.5 9.5.5 5.5.5 1.8z"/></svg></li>
      <li>ned@harborlawgroup.example
        <svg viewBox="0 0 10 10"><path d="M0 2h10v6H0zm.8.6L5 5.6l4.2-3z" fill-rule="evenodd"/></svg></li>
      <li>www.harborlawgroup.example
        <svg viewBox="0 0 10 10"><circle cx="5" cy="5" r="4.3" fill="none" stroke="var(--gold)" stroke-width="0.9"/><path d="M.7 5h8.6M5 .7v8.6" stroke="var(--gold)" stroke-width="0.7"/></svg></li>
    </ul>

    <article class="letter">
      <p class="salutation">Dear Mr. Carter,</p>
      <p class="body">Lorem ipsum dolor sit amet, consectetur adipiscing elit. Donec orci purus, luctus vitae dignissim eu, iaculis sed purus. Vivamus faucibus, ipsum nec aliquet viverra, leo mauris condimentum ligula, sit amet sagittis enim ligula quis arcu. Nam egestas tortor id nisi porttitor mattis. In tortor ante, ultricies in suscipit a, tempus non massa. Vivamus et auctor mi. Fusce vel massa nulla. Phasellus nec eros mauris, et scelerisque orci.</p>
      <p class="body">Donec malesuada orci vitae nulla accumsan porta a id massa. Quisque accumsan iaculis magna sit amet fringilla. Maecenas consequat, magna eget tincidunt semper, odio nibh rutrum mi, id feugiat ante nisi eu risus. Vestibulum nunc orci, rhoncus a placerat in, ultricies in mi. Cras mattis varius eros, vel fringilla nisi suscipit eget. Quisque scelerisque sagittis nulla at porttitor.</p>
      <p class="body">Sed id augue vitae urna euismod commodo aliquet a quam. Pellentesque arcu velit, cursus et malesuada ut, consequat et diam. Nullam erat sem, rhoncus id ullamcorper vitae, rhoncus et arcu. In ultricies ultricies nulla, ut rutrum nisi iaculis at. Donec eu magna a metus ornare faucibus. Fusce aliquet faucibus ultricies. Morbi semper, est id tincidunt gravida, sem arcu adipiscing lacus, ac bibendum nulla leo eu purus. Quisque nec diam sed risus consectetur a accumsan quis quis nibh. Vestibulum id purus lorem.</p>
      <p class="closing">Sincerely,</p>
      <span class="signature" role="img" aria-label="Handwritten signature"></span>
    </article>

    <footer class="practice-footer">
      <p class="practice-areas">Personal Injury • Injunctions •&nbsp;&nbsp; Criminal Defense • Family Law</p>
      <div class="badges">
        <span class="badge red"></span>
        <span class="badge gold"></span>
      </div>
    </footer>
  </section>

  <section class="sheet envelope-back">
    <svg class="wave" width="508" height="90" viewBox="0 0 508 90">
      <path d="M0 0 H508 L490 55 Q484 81 455 81 H65 Q35 81 28 60 Z" fill="var(--navy)"/>
    </svg>
    <div class="flap-mark">Harbor Law</div>
  </section>

  <section class="sheet envelope-front">
    <svg class="wave" width="510" height="120" viewBox="0 0 510 120">
      <path d="M0 0 H510 V25 C470 10 400 12 330 40 C240 75 170 115 100 110 C50 106 20 95 0 88 Z" fill="var(--navy)"/>
    </svg>
    <div class="brand">
      <span class="brand-dot"></span>
      <div>
        <div class="brand-name">Harbor Law</div>
        <p class="return-address">48 Quayside Avenue<br>Port Wren, Maine 04112</p>
      </div>
    </div>
  </section>

</body>
</html>
```